One Page Website for Personal Trainer in London

I have a logo and need a one page website designed around my branding. I am a freelance Personal Trainer based in London specialising in bodyweight training for men and women. I would like the site to be modern and clean but not overtly urban in design.
I need the following headings:
About Me
My Services
Events
Blog
I don't need them to be seperate pages but if they can link to further down the page that would be great.
Industry/Entity Type
Personal Trainer
Coding
Coded - Design and coding required
Number of Pages Required
1 page
Requirements
Must have
- I need the following headings:
- About Me
- My Services
- Events
- Blog
- mobile friendly formatting
- health and fitness related photography
- Colour scheme in keeping with my existing logo

```html
<!DOCTYPE html>
<html lang="en">
<head>
<meta charset="utf-8">
<title>Marlow Reid – Personal Training</title>
<link rel="stylesheet" href="https://fonts.googleapis.com/css2?family=Montserrat:wght@400;600;700&family=Open+Sans:wght@400;600;700&display=swap">
<style>
:root{
  --orange:#f39a1e;
  --ink:#1f1f1f;
  --text:#555;
  --muted:#8a8a8a;
  --dark:#1a1a1a;
  --white:#fff;
}
*{margin:0;padding:0;box-sizing:border-box}
html,body{width:1200px;height:3805px;overflow:hidden;background:var(--white)}
body{position:relative;font-family:"Open Sans",Arial,sans-serif;color:var(--text)}
.abs{position:absolute}
h1,h2,h3,.nav a,.btn,.heading{font-family:"Montserrat",Arial,sans-serif}

/* header */
.site-header{left:0;top:0;width:1200px;height:84px;background:var(--white);z-index:3}
.brand{left:76px;top:-50px;width:240px;height:240px;border-radius:50%;background:var(--white);z-index:4;display:flex;align-items:flex-end;justify-content:center;padding-bottom:62px}
.brand-name{font-family:"Montserrat",Arial,sans-serif;font-weight:700;font-size:25px;color:var(--orange);letter-spacing:.5px}
.nav{right:96px;top:0;height:84px;display:flex;align-items:center;gap:32px;z-index:4}
.nav a{font-size:14px;font-weight:600;color:var(--ink);text-decoration:none;text-transform:uppercase}
.nav a.active{color:var(--orange)}

/* hero */
.hero{left:0;top:84px;width:1200px;height:474px;background:
  radial-gradient(ellipse 30% 40% at 85% 30%,rgba(120,110,90,.55),transparent 70%),
  radial-gradient(ellipse 25% 45% at 18% 35%,rgba(60,70,90,.6),transparent 70%),
  linear-gradient(180deg,#7d8ea8 0%,#566680 35%,#2f3549 62%,#8a6a3e 78%,#3b3a44 88%,#1f2334 100%)}
.hero-title{left:0;top:200px;width:1200px;text-align:center;font-size:60px;font-weight:700;color:var(--white);letter-spacing:1px}
.hero-sub{left:0;top:284px;width:1200px;text-align:center;font-size:20px;font-weight:600;line-height:32px;color:var(--white)}
.btn{display:inline-flex;align-items:center;justify-content:center;background:var(--orange);color:var(--white);font-weight:700;font-size:14px;text-transform:uppercase;border-radius:3px}
.hero-btn{left:520px;top:375px;width:160px;height:42px}
.dots{left:572px;top:502px;display:flex;gap:5px}
.dots span{width:10px;height:10px;border-radius:50%;border:1.5px solid var(--white)}
.dots span.on{background:var(--white)}

/* about */
.about-frame{left:119px;top:646px;width:383px;height:462px;border:2px solid #f3c27a}
.about-photo{left:101px;top:660px;width:388px;height:461px;background:
  radial-gradient(ellipse 35% 30% at 45% 50%,rgba(220,190,160,.6),transparent 70%),
  linear-gradient(180deg,#6e4a35 0%,#a7714d 15%,#c79a72 35%,#7d8f9c 58%,#9aa6ad 70%,#c2ae96 85%,#a89278 100%)}
.about-title{left:576px;top:658px;font-size:34px;font-weight:700;color:var(--ink)}
.about-text{left:576px;width:523px;font-size:13px;line-height:28px;color:var(--muted)}
.btn-outline{left:576px;top:1050px;width:127px;height:41px;border:1.5px solid #bbb;border-radius:3px;display:flex;align-items:center;justify-content:center;font-family:"Montserrat",Arial,sans-serif;font-size:13px;font-weight:700;color:var(--orange)}

/* program */
.program{left:0;top:1230px;width:1200px;height:546px;background:linear-gradient(90deg,#2a2624 0%,#4a4440 45%,#23201f 100%)}
.program-photo{left:520px;top:1230px;width:622px;height:546px;background:
  radial-gradient(ellipse 22% 50% at 30% 60%,rgba(200,150,120,.75),transparent 70%),
  radial-gradient(ellipse 26% 55% at 68% 58%,rgba(210,160,125,.8),transparent 70%),
  radial-gradient(ellipse at 50% 45%,#6a5446 0%,#43362e 55%,#231f1d 100%)}
.program-title{left:114px;top:1285px;font-size:31px;line-height:45px;font-weight:700;color:var(--white)}
.checklist{left:114px;top:1402px;list-style:none}
.checklist li{display:flex;align-items:center;gap:14px;height:32.6px;font-size:17px;font-weight:600;color:var(--white)}
.program-btn{left:114px;top:1629px;width:152px;height:46px}
.program-curve{left:0;top:1640px}

/* blog */
.section-title{left:0;width:1200px;text-align:center;font-size:34px;font-weight:600;color:var(--ink)}
.post{width:322px}
.post-img{width:322px;height:182px}
.post-title{margin-top:34px;font-size:18px;font-weight:700;color:var(--ink);font-family:"Open Sans",Arial,sans-serif}
.post-meta{margin-top:10px;font-size:12px;color:var(--muted);display:flex;align-items:center;gap:6px}
.post-text{margin-top:10px;font-size:13px;line-height:22px;color:var(--muted)}
.read-more{margin-top:26px;font-size:12px;font-weight:700;color:var(--orange);text-transform:uppercase;font-family:"Montserrat",Arial,sans-serif}

/* newsletter */
.newsletter{left:0;top:2347px;width:1200px;height:291px;background:
  radial-gradient(ellipse 20% 60% at 20% 60%,rgba(170,95,30,.45),transparent 70%),
  radial-gradient(ellipse 20% 60% at 82% 55%,rgba(170,95,30,.4),transparent 70%),
  linear-gradient(90deg,#d9822a 0%,#f0a23f 50%,#d98a35 100%)}
.newsletter-title{left:0;top:2410px;width:1200px;text-align:center;font-size:32px;font-weight:700;color:var(--white)}
.newsletter-sub{left:0;top:2463px;width:1200px;text-align:center;font-size:17px;font-weight:600;color:var(--white)}
.email-field{left:282px;top:2517px;width:474px;height:53px;background:var(--white);display:flex;align-items:center;padding-left:24px;font-size:13px;color:#777;text-transform:uppercase}
.email-btn{left:756px;top:2517px;width:162px;height:53px;background:var(--dark);border-radius:0}

/* stories */
.story{width:240px;height:345px;top:2811px;border:1px solid #e6e6e6;background:var(--white);text-align:center;overflow:hidden}
.story-img{width:238px;height:183px;clip-path:ellipse(90% 100% at 50% 0%)}
.story-name{margin-top:16px;font-size:17px;font-weight:600;color:var(--ink)}
.story-text{margin:8px auto 0;width:190px;font-size:12px;line-height:21px;color:var(--muted)}
.story-more{margin-top:6px;font-size:12px;font-weight:700;color:var(--orange);font-family:"Montserrat",Arial,sans-serif}
.slider-arrow{top:2892px;width:40px;height:40px;border-radius:50%;border:1px solid #ccc;background:var(--white);display:flex;align-items:center;justify-content:center}

/* contact */
.contact{left:0;top:3247px;width:1200px;height:558px;background:
  radial-gradient(ellipse 25% 45% at 30% 35%,rgba(90,85,80,.5),transparent 70%),
  linear-gradient(180deg,#2e2e2e 0%,#161616 100%)}
.contact-curve{left:0;top:3247px}
.contact-title{left:0;top:3313px;width:1200px;text-align:center;font-size:34px;font-weight:600;color:var(--white)}
.col-title{top:3400px;font-size:17px;font-weight:600;color:var(--white)}
.field{border:1px solid #8a8a8a;height:36px;font-size:12px;color:#ddd;padding:9px 10px}
.submit{left:647px;top:3653px;width:81px;height:31px;font-size:12px}
.info-row{left:782px;display:flex;align-items:center;gap:22px;font-size:12px;line-height:20px;color:#ddd}
.info-icon{width:40px;height:40px;border-radius:50%;background:#2f2f2f;display:flex;align-items:center;justify-content:center;flex:none}
.socials{left:788px;top:3657px;display:flex;gap:14px}
.socials span{width:29px;height:29px;border-radius:50%}
.footer-line{left:96px;top:3724px;width:1008px;height:1px;background:#444}
.copyright{left:0;top:3759px;width:1200px;text-align:center;font-size:12px;color:#bbb}
.to-top{left:1098px;top:3760px}
</style>
</head>
<body>

<header class="site-header abs"></header>
<div class="brand abs"><span class="brand-name">Marlow Reid</span></div>
<nav class="nav abs">
  <a class="active" href="#home">Home</a>
  <a href="#about">About Me</a>
  <a href="#services">My Services</a>
  <a href="#events">Events</a>
  <a href="#blog">Blog</a>
  <a href="#contact">Contact</a>
  <svg width="14" height="14" viewBox="0 0 14 14"><circle cx="6" cy="6" r="4.5" fill="none" stroke="#1f1f1f" stroke-width="2"/><line x1="9.3" y1="9.3" x2="13" y2="13" stroke="#1f1f1f" stroke-width="2"/></svg>
</nav>

<section id="home">
  <div class="hero abs" role="img" aria-label="Photo: London skyline at dusk with river reflections"></div>
  <h1 class="hero-title abs">MARLOW REID</h1>
  <p class="hero-sub abs">We are a freelance Personal Trainer based in London specialising<br>in bodyweight training for men and women</p>
  <span class="btn hero-btn abs">Get Started</span>
  <div class="dots abs"><span class="on"></span><span></span><span></span><span></span></div>
</section>

<section id="about">
  <div class="about-frame abs"></div>
  <div class="about-photo abs" role="img" aria-label="Photo: trainer walking along a beach at sunset"></div>
  <h2 class="about-title abs">ABOUT ME</h2>
  <p class="about-text abs" style="top:727px">Every session is built around your own body weight, so you can train anywhere, at any time, and still see steady progress week after week.</p>
  <p class="about-text abs" style="top:811px">I started coaching after years of training clients in busy London gyms and realising that most people do not need machines to get strong. What they need is a clear plan, honest feedback and someone who keeps them moving. My programmes mix strength, mobility and conditioning, with simple meals that fit a normal week and a pace that suits your starting point. Sessions run outdoors or at home, in parks across the city, and every plan is reviewed each month so it keeps up with you as you get fitter and more confident.</p>
  <div class="btn-outline abs">READ MORE</div>
</section>

<section id="services">
  <div class="program abs"></div>
  <div class="program-photo abs" role="img" aria-label="Photo: smiling fitness couple holding a towel and water bottle"></div>
  <h2 class="program-title abs">WHAT’S INCLUDED IN<br>THE PROGRAM?</h2>
  <ul class="checklist abs">
    <li><svg width="18" height="18" viewBox="0 0 18 18"><circle cx="9" cy="9" r="9" fill="#fff"/><path d="M5 9.3l2.6 2.6L13 6.5" fill="none" stroke="#2a2624" stroke-width="2"/></svg>Built for Men &amp; Women</li>
    <li><svg width="18" height="18" viewBox="0 0 18 18"><circle cx="9" cy="9" r="9" fill="#fff"/><path d="M5 9.3l2.6 2.6L13 6.5" fill="none" stroke="#2a2624" stroke-width="2"/></svg>No Equipment Necessary</li>
    <li><svg width="18" height="18" viewBox="0 0 18 18"><circle cx="9" cy="9" r="9" fill="#fff"/><path d="M5 9.3l2.6 2.6L13 6.5" fill="none" stroke="#2a2624" stroke-width="2"/></svg>30 Minute Workouts or Less</li>
    <li><svg width="18" height="18" viewBox="0 0 18 18"><circle cx="9" cy="9" r="9" fill="#fff"/><path d="M5 9.3l2.6 2.6L13 6.5" fill="none" stroke="#2a2624" stroke-width="2"/></svg>Full 30 Day Vegan Meal Plan</li>
    <li><svg width="18" height="18" viewBox="0 0 18 18"><circle cx="9" cy="9" r="9" fill="#fff"/><path d="M5 9.3l2.6 2.6L13 6.5" fill="none" stroke="#2a2624" stroke-width="2"/></svg>Nutritional Guidance</li>
    <li><svg width="18" height="18" viewBox="0 0 18 18"><circle cx="9" cy="9" r="9" fill="#fff"/><path d="M5 9.3l2.6 2.6L13 6.5" fill="none" stroke="#2a2624" stroke-width="2"/></svg>Physical Therapy</li>
  </ul>
  <span class="btn program-btn abs">Get Started</span>
  <svg class="program-curve abs" width="1200" height="137" viewBox="0 0 1200 137"><path d="M0 137 Q600 -10 1200 137 Z" fill="#fff"/></svg>
</section>

<section id="blog">
  <h2 class="section-title abs" style="top:1808px">LATEST BLOG</h2>
  <article class="post abs" style="left:99px;top:1893px">
    <div class="post-img" role="img" aria-label="Photo: women running on treadmills in a gym" style="background:radial-gradient(ellipse 30% 60% at 65% 50%,rgba(230,200,175,.7),transparent 70%),linear-gradient(135deg,#c9a98f,#8a6f62 55%,#3e3a3c)"></div>
    <h3 class="post-title">Finibus Bonorum et Malorum</h3>
    <div class="post-meta"><svg width="12" height="12" viewBox="0 0 12 12"><rect x="1" y="2" width="10" height="9" fill="none" stroke="#f39a1e" stroke-width="1.5"/><line x1="1" y1="5" x2="11" y2="5" stroke="#f39a1e" stroke-width="1.5"/></svg>July 2nd, 2015 &nbsp;| <svg width="12" height="12" viewBox="0 0 12 12"><path d="M1 2h10v6H5l-3 3V8H1z" fill="none" stroke="#f39a1e" stroke-width="1.3"/></svg>0 Comments</div>
    <p class="post-text">Simple steps to build strength at home with nothing but your own body weight.</p>
    <div class="read-more">Read More</div>
  </article>
  <article class="post abs" style="left:439px;top:1893px">
    <div class="post-img" role="img" aria-label="Photo: loaded barbell on a gym floor" style="background:radial-gradient(ellipse 40% 35% at 50% 75%,rgba(120,125,130,.6),transparent 70%),linear-gradient(135deg,#3a3f48,#1d2026 60%,#4a4f57)"></div>
    <h3 class="post-title">Finibus Bonorum et Malorum</h3>
    <div class="post-meta"><svg width="12" height="12" viewBox="0 0 12 12"><rect x="1" y="2" width="10" height="9" fill="none" stroke="#f39a1e" stroke-width="1.5"/><line x1="1" y1="5" x2="11" y2="5" stroke="#f39a1e" stroke-width="1.5"/></svg>July 2nd, 2015 &nbsp;| <svg width="12" height="12" viewBox="0 0 12 12"><path d="M1 2h10v6H5l-3 3V8H1z" fill="none" stroke="#f39a1e" stroke-width="1.3"/></svg>0 Comments</div>
    <p class="post-text">Simple steps to build strength at home with nothing but your own body weight.</p>
    <div class="read-more">Read More</div>
  </article>
  <article class="post abs" style="left:779px;top:1893px">
    <div class="post-img" role="img" aria-label="Photo: woman training with a cable machine" style="background:radial-gradient(ellipse 25% 55% at 55% 55%,rgba(200,165,140,.7),transparent 70%),linear-gradient(135deg,#4f6575,#2c3a45 55%,#a08a7a)"></div>
    <h3 class="post-title">Finibus Bonorum et Malorum</h3>
    <div class="post-meta"><svg width="12" height="12" viewBox="0 0 12 12"><rect x="1" y="2" width="10" height="9" fill="none" stroke="#f39a1e" stroke-width="1.5"/><line x1="1" y1="5" x2="11" y2="5" stroke="#f39a1e" stroke-width="1.5"/></svg>July 2nd, 2015 &nbsp;| <svg width="12" height="12" viewBox="0 0 12 12"><path d="M1 2h10v6H5l-3 3V8H1z" fill="none" stroke="#f39a1e" stroke-width="1.3"/></svg>0 Comments</div>
    <p class="post-text">Simple steps to build strength at home with nothing but your own body weight.</p>
    <div class="read-more">Read More</div>
  </article>
</section>

<section id="events">
  <div class="newsletter abs" role="img" aria-label="Photo: group doing bodyweight exercises, orange tinted"></div>
  <h2 class="newsletter-title abs">BODYWEIGHT TRAINING: EPIC GUIDES</h2>
  <p class="newsletter-sub abs">Register your Email Address to get Epic &amp; Actionable content</p>
  <div class="email-field abs">Email Address</div>
  <span class="btn email-btn abs">Get Started</span>
</section>

<section id="stories">
  <h2 class="section-title abs" style="top:2726px">SUCCESS STORIES</h2>
  <div class="slider-arrow abs" style="left:43px"><svg width="10" height="12" viewBox="0 0 10 12"><path d="M7 1L2 6l5 5" fill="none" stroke="#888" stroke-width="1.5"/></svg></div>
  <div class="slider-arrow abs" style="left:1117px"><svg width="10" height="12" viewBox="0 0 10 12"><path d="M3 1l5 5-5 5" fill="none" stroke="#888" stroke-width="1.5"/></svg></div>
  <div class="story abs" style="left:99px">
    <div class="story-img" role="img" aria-label="Photo: before and after shots of a client" style="background:linear-gradient(90deg,#e6d5cc,#d9b7a4 25%,#f0e8e2 50%,#b88a78 70%,#5b7aa0)"></div>
    <div class="story-name">Felicia</div>
    <p class="story-text">Lost ten kilos in twelve weeks and now trains four times a week with real joy.</p>
    <div class="story-more">READ MORE &gt;&gt;</div>
  </div>
  <div class="story abs" style="left:353px">
    <div class="story-img" role="img" aria-label="Photo: before and after shots of a client" style="background:linear-gradient(90deg,#e8e6e4,#cfa48a 25%,#f2f0ee 50%,#a87c66 75%,#e8e6e4)"></div>
    <div class="story-name">Adam</div>
    <p class="story-text">Built real strength at home and finished his first half marathon this spring.</p>
    <div class="story-more">READ MORE &gt;&gt;</div>
  </div>
  <div class="story abs" style="left:609px">
    <div class="story-img" role="img" aria-label="Photo: before and after shots of a client" style="background:linear-gradient(90deg,#c4a08e,#8a95a8 35%,#e0d6cf 50%,#d1ad98 75%,#6f6a72)"></div>
    <div class="story-name">Clara</div>
    <p class="story-text">Gained energy, confidence and a steady routine that fits neatly around her job.</p>
    <div class="story-more">READ MORE &gt;&gt;</div>
  </div>
  <div class="story abs" style="left:861px">
    <div class="story-img" role="img" aria-label="Photo: before and after shots of a client" style="background:linear-gradient(90deg,#e9e3dc,#b7866c 30%,#f1ebe5 50%,#d4a98c 70%,#9c6f58)"></div>
    <div class="story-name">John</div>
    <p class="story-text">Dropped two sizes in four months and can now do twenty clean push ups.</p>
    <div class="story-more">READ MORE &gt;&gt;</div>
  </div>
</section>

<section id="contact">
  <div class="contact abs" role="img" aria-label="Photo: dark gym background with athlete training"></div>
  <svg class="contact-curve abs" width="1200" height="70" viewBox="0 0 1200 70"><path d="M0 0H1200V60Q600 -40 0 60Z" fill="#fff"/></svg>
  <h2 class="contact-title abs">CONTACT US</h2>
  <h3 class="col-title abs" style="left:96px">Contact Form</h3>
  <div class="field abs" style="left:96px;top:3463px;width:313px">Name</div>
  <div class="field abs" style="left:419px;top:3463px;width:309px">Phone no</div>
  <div class="field abs" style="left:96px;top:3509px;width:632px;height:33px;padding-top:7px">Email</div>
  <div class="field abs" style="left:96px;top:3554px;width:632px;height:82px">Message</div>
  <span class="btn submit abs">Submit</span>

  <h3 class="col-title abs" style="left:781px">Contact Information</h3>
  <div class="info-row abs" style="top:3451px">
    <span class="info-icon"><svg width="12" height="16" viewBox="0 0 12 16"><path d="M6 0a6 6 0 0 1 6 6c0 4-6 10-6 10S0 10 0 6a6 6 0 0 1 6-6z" fill="#fff"/><circle cx="6" cy="6" r="2.2" fill="#2f2f2f"/></svg></span>
    <span>14 Kestrel Lane<br>Suite 8 London, E2 7QA</span>
  </div>
  <div class="info-row abs" style="top:3504px">
    <span class="info-icon"><svg width="14" height="14" viewBox="0 0 14 14"><path d="M3 0l3 3-2 2c1 2 3 4 5 5l2-2 3 3-2 3C6 14 0 8 0 3z" fill="#fff"/></svg></span>
    <span>1 555 010 2040</span>
  </div>
  <div class="info-row abs" style="top:3555px">
    <span class="info-icon"><svg width="16" height="12" viewBox="0 0 16 12"><rect width="16" height="12" rx="1" fill="#fff"/><path d="M0 1l8 6 8-6" fill="none" stroke="#2f2f2f" stroke-width="1.3"/></svg></span>
    <span>info@marlowreid.com</span>
  </div>
  <h3 class="col-title abs" style="left:781px;top:3613px">Social Media</h3>
  <div class="socials abs"><span style="background:#3b5998"></span><span style="background:#29a9e1"></span><span style="background:#0e76a8"></span><span style="background:#dd4b39"></span><span style="background:#c47a5a"></span></div>

  <div class="footer-line abs"></div>
  <p class="copyright abs">Copyright © 2017, Marlow Reid. All rights reserved.</p>
  <svg class="to-top abs" width="36" height="20" viewBox="0 0 36 20"><path d="M3 17L18 3l15 14" fill="none" stroke="#fff" stroke-width="3"/></svg>
</section>

</body>
</html>
```